Coastal Learner Bureau business cards

Australian company about to start offering its services. We recruit international students to come to study English, vocational education and postgraduate courses in Australia. We help them find the institution and select the right city they want to come to Australia. We are a young, online oriented and supportive agency. Our clients are between 18 and 35 years old, mainly University students, young professionals or people with work experience. We provide much more information that any other agency offer. We administrate a Facebook group with more than 11.000 members that daily ask questions about general information when coming to Australia, while they are here and even after they leave the country

Target Market(s)

International students from South America, Central America and Europe

Industry/Entity Type

Student

Contact Information for Business Card

Tomas Bilbrea
Managing Director
tomas@kelvarin.com.au
www.kelvoria.com.au
+61 491058264
Melbourne, Australia

Font styles to use
Serif
Sans Serif

Colors

Designer to choose colors to be used in the design.

Requirements
Must have
• Horizontal design
• Standard business card size and shape. If font uses green or yellow colours, they will have to match the ones from the logo
Nice to have
• UPDATE: Use the contents of the green image to design one of the card sides. Use our logo in the background of that side as watermark.
• Passport image, or immigration stamps. A picture of the Yarra River (from Melbourne) would be cool as well.
Should not have
• Non-standard business card size and shape
• Not black as the background colour of any sides as we are not a VIP agency or a hight class service. We are orientes to young people and they like colours, pictures, something attractive.
• Vertical design
• NO YELLOW or BLACK AS THE BACKGROUND COLOUR OF ANY SIDE OF THE BIZ CARD

```html
<!DOCTYPE html>
<html lang="en">
<head>
<meta charset="utf-8">
<title>Coastal Learner Bureau business cards</title>
<link href="https://fonts.googleapis.com/css2?family=Comic+Neue:wght@700&family=Open+Sans:wght@400;600&display=swap" rel="stylesheet">
<style>
  :root {
    --brand-green: #0f6a40;
    --brand-green-light: #1d7f50;
    --brand-yellow: #e9b91b;
    --card-white: #f4f4f4;
    --ink-grey: #4a4a4a;
    --rule-grey: #9a9a9a;
    --page-bg: #e6e3df;
    --text-white: #ffffff;
  }
  * { margin: 0; padding: 0; box-sizing: border-box; }
  html, body {
    width: 1200px; height: 886px; overflow: hidden;
    background: var(--page-bg);
    font-family: "Open Sans", Arial, sans-serif;
  }
  .canvas { position: relative; width: 1200px; height: 886px; }

  .card {
    position: absolute;
    width: 560px; height: 320px;
    border-radius: 18px;
    overflow: hidden;
    box-shadow: 0 10px 24px rgba(0,0,0,.18);
  }

  /* Front side */
  .card-front { left: 70px; top: 80px; background: var(--card-white); }
  .brand {
    position: absolute; left: 0; right: 0; top: 105px;
    display: flex; align-items: center; justify-content: center; gap: 12px;
  }
  .brand-dot {
    width: 22px; height: 22px; border-radius: 50%;
    background: var(--brand-yellow);
  }
  .brand-name {
    font-family: "Comic Neue", "Comic Sans MS", cursive;
    font-weight: 700; font-size: 58px; color: var(--brand-green);
    letter-spacing: .5px;
  }
  .tagline-row {
    position: absolute; left: 60px; right: 60px; top: 228px;
    display: flex; align-items: center; gap: 10px;
  }
  .tagline-rule { flex: 1; height: 1px; background: var(--rule-grey); }
  .tagline {
    font-size: 13px; font-weight: 600; color: var(--ink-grey);
    white-space: nowrap;
  }

  /* Back side */
  .card-back { left: 570px; top: 480px; background: var(--brand-green); }
  .watermark {
    position: absolute; right: 30px; top: 26px;
    width: 260px; height: 200px;
    border-radius: 40px 60px 70px 50px;
    background: radial-gradient(ellipse at 45% 40%, var(--brand-green-light) 0%, var(--brand-green-light) 55%, rgba(233,185,27,.35) 100%);
  }
  .contact {
    position: absolute; left: 34px; bottom: 30px;
    color: var(--text-white);
  }
  .contact-name {
    font-family: "Comic Neue", "Comic Sans MS", cursive;
    font-weight: 700; font-size: 24px; color: var(--brand-yellow);
    line-height: 1.1;
  }
  .contact-role { font-size: 14px; font-weight: 600; margin-top: 2px; }
  .contact-city { font-size: 12px; margin-top: 6px; margin-bottom: 8px; }
  .contact-list { list-style: none; }
  .contact-list li {
    display: flex; align-items: center; gap: 8px;
    font-size: 12px; line-height: 19px;
  }
  .contact-icon { width: 12px; height: 12px; flex: none; }
</style>
</head>
<body>
<main class="canvas">

  <section class="card card-front" aria-label="Card front">
    <div class="brand">
      <span class="brand-dot"></span>
      <span class="brand-name">Kelvoria</span>
    </div>
    <div class="tagline-row">
      <span class="tagline-rule"></span>
      <span class="tagline">Hacemos más por ti!</span>
      <span class="tagline-rule"></span>
    </div>
  </section>

  <section class="card card-back" aria-label="Card back">
    <div class="watermark" role="img" aria-label="Large outline of the brand mark as a background watermark"></div>
    <div class="contact">
      <p class="contact-name">Tomas Bilbrea</p>
      <p class="contact-role">Managing Director</p>
      <p class="contact-city">Melbourne, Australia</p>
      <ul class="contact-list">
        <li>
          <svg class="contact-icon" viewBox="0 0 12 12" aria-hidden="true">
            <path d="M2.5 1 L4.5 1 L5 3.5 L3.8 4.4 Q5 7 7.6 8.2 L8.5 7 L11 7.5 L11 9.5 Q11 11 9.5 11 Q1 10 1 2.5 Q1 1 2.5 1 Z" fill="var(--brand-yellow)"/>
          </svg>
          +61 491058264
        </li>
        <li>
          <svg class="contact-icon" viewBox="0 0 12 12" aria-hidden="true">
            <rect x="0.5" y="2" width="11" height="8" rx="1" fill="var(--brand-yellow)"/>
            <path d="M1 2.6 L6 6.5 L11 2.6" stroke="var(--brand-green)" stroke-width="1.1" fill="none"/>
          </svg>
          tomas@kelvarin.com.au
        </li>
        <li>
          <svg class="contact-icon" viewBox="0 0 12 12" aria-hidden="true">
            <circle cx="6" cy="6" r="5.5" fill="var(--brand-yellow)"/>
            <path d="M0.8 6 H11.2 M6 0.6 Q3 6 6 11.4 M6 0.6 Q9 6 6 11.4" stroke="var(--brand-green)" stroke-width="0.9" fill="none"/>
          </svg>
          www.kelvoria.com.au
        </li>
      </ul>
    </div>
  </section>

</main>
</body>
</html>
```